Brochure for a civil enineering company in A4 format

I need a brochure design for our company TIRO Engineering S.r.l.. We are an engineering consultant company. Our main clients are from the infrastructure industry (geotechnical and underground sectors mainly).
We are looking for a 2 pages (4 faces) fold out design with a glued pocket where we can put individual data sheets.
I need A4 format pages.

Target Market(s)

We are an engineering consultant company. Our main clients are from the infrastructure industry (geotechnical and underground sectors mainly).

Industry/Entity Type

Civil Engineer

Font styles to use
Sans Serif

Requirements
Must have
• Overall: 2 pages in A4 format
Essential style. Bright and modern appearance.
Glued pocket
Logo integrated in a picture on the pocket where I would like to insert a slogan (… tiro engineering … reliable solutions …)
Attached are selected images which the designer can use and edit at their own discretion.
Some advice in the following (anyway designers are free to provide their solutions):
Outer sheets:
Front page with name, logo. It could be nice to have the “m” of the logo integrated in a pictures, also a modified picture (I mean modify one of the attached pictures) so to create a general image and do not tie the cover to a specific job.
Back page: offices address and contact email address. Nice to have one space for a slogan.
Inner sheet: text that I upload in the file “inside-sheets”, possibly with pictures on each sheet. In the right faces insert the glued pocket. On this pages insert the section OUR EXPERIENCE ….with a space for a picture of our team.
Nice to have
• Clean and essential design.
Pictures choosing from the atteched ones. Pictures could be modified in a very light manner to make them a general idea of the work ( I mean geotechnical world) without to be immediately linked to a specific site.
Should not have
• excessive frills

```html
<!DOCTYPE html>
<html lang="it">
<head>
<meta charset="utf-8">
<title>TIRO Engineering – Brochure</title>
<link href="https://fonts.googleapis.com/css2?family=Barlow+Condensed:wght@600;700&family=Didact+Gothic&family=Questrial&display=swap" rel="stylesheet">
<style>
  :root {
    --bg: #848560;
    --teal-dark: #0d4a63;
    --navy: #0f3d55;
    --green: #168a6c;
    --mint: #38bfa2;
    --yellow: #f3c11c;
    --yellow-pale: #f5dd8a;
    --paper: #e8f1ef;
    --white: #ffffff;
    --ink: #1d2a30;
  }
  * { box-sizing: border-box; margin: 0; padding: 0; }
  html, body { width: 1200px; height: 1200px; overflow: hidden; background: var(--bg); }
  .canvas { position: relative; width: 1200px; height: 1200px; overflow: hidden; background: var(--bg); font-family: "Didact Gothic", sans-serif; color: var(--ink); }
  .abs { position: absolute; }
  .photo { position: absolute; }
  .sheet { position: absolute; box-shadow: 0 6px 14px rgba(0,0,0,.28); }

  /* ---------- outer sheet ---------- */
  .outer { left: 81px; top: 75px; width: 864px; height: 406px; }
  .panel-sky { background: linear-gradient(180deg, #6f9be0 0%, #a8c4ea 60%, #c9d8ea 100%); }
  .panel-network { background: radial-gradient(circle at 40% 30%, #1f5a78 0%, #154b68 45%, #0f3a56 100%); }
  .band { position: absolute; height: 34px; }
  .band-green { background: var(--green); }
  .band-teal { background: rgba(20,110,125,.85); }
  .band-text { position: absolute; font-family: "Barlow Condensed", sans-serif; font-weight: 700; font-size: 29px; line-height: 34px; color: var(--white); letter-spacing: .5px; }
  .offices { position: absolute; color: var(--white); font-size: 4.8px; line-height: 1.35; }
  .offices .label { font-family: "Questrial", sans-serif; font-weight: 700; font-size: 5px; }
  .offices .city { font-weight: 700; }
  .site { position: absolute; left: 386px; top: 457px; color: var(--white); font-family: "Questrial", sans-serif; font-size: 6px; letter-spacing: 2.6px; }
  .brand-name { position: absolute; color: var(--white); font-family: "Questrial", sans-serif; }
  .brand-small { left: 587px; top: 445px; font-size: 19px; line-height: 1; }
  .brand-big { left: 700px; top: 98px; width: 206px; text-align: center; font-size: 72px; line-height: 1; letter-spacing: 2px; }
  .tagline { position: absolute; left: 699px; top: 166px; width: 206px; text-align: center; color: var(--white); font-size: 6px; letter-spacing: 2.1px; }
  .cover-band { position: absolute; }
  .cover-dark { background: var(--navy); }
  .cover-mint { background: var(--mint); }
  .cover-text { position: absolute; font-family: "Barlow Condensed", sans-serif; font-weight: 600; color: var(--white); line-height: 1; }
  .sector-tag { position: absolute; left: 784px; top: 261px; width: 126px; height: 11px; background: var(--yellow); clip-path: polygon(3% 0, 100% 0, 97% 100%, 0 100%); font-family: "Barlow Condensed", sans-serif; font-weight: 700; font-size: 6.2px; line-height: 11px; text-align: center; color: var(--ink); }

  /* ---------- inner sheet ---------- */
  .inner { left: 228px; top: 540px; width: 867px; height: 408px; background: var(--paper); }
  .pocket { position: absolute; left: 806px; top: 948px; width: 289px; height: 157px; background: #0a4a62; clip-path: polygon(0 0, 100% 0, 100% 100%, 6% 100%); }
  .section-title { position: absolute; color: var(--white); font-family: "Questrial", sans-serif; line-height: 1; white-space: nowrap; }
  .section-title b { font-weight: 700; font-family: "Didact Gothic", sans-serif; }
  .copy { position: absolute; font-size: 4.4px; line-height: 1.32; color: var(--ink); }
  .copy p { margin-bottom: 2.6px; }
  .copy-lg { font-size: 5.5px; line-height: 1.22; }
  .copy ul { list-style: none; }
  .copy li { margin-bottom: 3.4px; padding-left: 5px; text-indent: -4px; }
  .copy li::before { content: "• "; }
  .yellow { position: absolute; background: var(--yellow); }
  .yellow-pale { position: absolute; background: var(--yellow-pale); }
</style>
</head>
<body>
<div class="canvas">

  <!-- OUTER SHEET: back, flap, front cover -->
  <section class="sheet outer" aria-label="Lato esterno della brochure">
    <div class="photo" style="left:0;top:0;width:288px;height:406px;background:linear-gradient(180deg,#78a6e6 0%,#a9c3e6 20%,#6d7a57 32%,#8d7a5e 45%,#6c5c48 65%,#4a3d33 100%);" role="img" aria-label="Montagne e cantiere in galleria con mezzi di scavo"></div>
    <svg class="abs" style="left:0;top:0" width="288" height="406" viewBox="0 0 288 406" aria-hidden="true">
      <polyline points="0,118 210,118 148,205 176,205 112,295 0,295" fill="none" stroke="#ffffff" stroke-width="6" stroke-linejoin="miter"/>
    </svg>
    <div class="photo panel-network" style="left:288px;top:0;width:288px;height:406px;" role="img" aria-label="Sfondo blu con rete di punti e linee luminose"></div>
    <div class="photo panel-sky" style="left:576px;top:0;width:288px;height:192px;" role="img" aria-label="Cielo azzurro"></div>
    <div class="photo" style="left:576px;top:192px;width:288px;height:214px;background:linear-gradient(180deg,#a39a8a 0%,#8a8478 35%,#b9b6b0 70%,#7f7a72 100%);" role="img" aria-label="Grande scavo di fondazione con gru e strutture in calcestruzzo"></div>
  </section>

  <!-- slogan bands across back and flap -->
  <div class="band band-green" style="left:267px;top:239px;width:102px;clip-path:polygon(14% 0,100% 0,100% 100%,0 100%);"></div>
  <div class="band band-teal" style="left:369px;top:239px;width:196px;clip-path:polygon(0 0,100% 0,92% 100%,0 100%);"></div>
  <div class="band band-green" style="left:242px;top:286px;width:127px;"></div>
  <div class="band band-teal" style="left:369px;top:286px;width:159px;clip-path:polygon(0 0,100% 0,92% 100%,0 100%);"></div>
  <div class="band-text" style="left:280px;top:239px;width:74px;text-align:right;">TIRO</div>
  <div class="band-text" style="left:386px;top:239px;">ENGINEERING</div>
  <div class="band-text" style="left:250px;top:286px;width:104px;text-align:right;">RELIABLE</div>
  <div class="band-text" style="left:386px;top:286px;">SOLUTIONS</div>

  <div class="offices" style="left:386px;top:379px;"><span class="label">OUR OFFICES</span></div>
  <div class="offices" style="left:386px;top:397px;">
    <div class="city">MILANO</div>
    <div>Via Verdi, 14 • 20100 Milano - IT</div>
    <div>T: +39 02 555 0147</div>
    <div>E: tiro_info@tiroengineering.org</div>
  </div>
  <div class="abs" style="left:487px;top:397px;width:1px;height:26px;background:rgba(255,255,255,.6);"></div>
  <div class="offices" style="left:497px;top:397px;">
    <div class="city">ARCO TN</div>
    <div>Via dei Tigli, 9 • 38062 Arco TN - IT</div>
    <div>T: +39 02 555 0147</div>
    <div>E: tiro_info@tiroengineering.org</div>
  </div>
  <div class="site">WWW.TIROENGINEERING.ORG</div>
  <div class="brand-name brand-small">tiro</div>

  <!-- front cover -->
  <div class="brand-name brand-big">tiro</div>
  <div class="tagline">TIRO ENGINEERING . RELIABLE SOLUTIONS</div>
  <div class="cover-band cover-dark" style="left:699px;top:200px;width:189px;height:25px;clip-path:polygon(8% 0,100% 0,96% 100%,0 100%);"></div>
  <div class="cover-band cover-dark" style="left:897px;top:200px;width:48px;height:25px;clip-path:polygon(22% 0,100% 0,100% 100%,0 100%);"></div>
  <div class="cover-band cover-mint" style="left:657px;top:225px;width:228px;height:36px;clip-path:polygon(0 0,100% 0,95% 100%,0 100%);"></div>
  <div class="cover-band cover-mint" style="left:870px;top:225px;width:75px;height:36px;clip-path:polygon(30% 0,100% 0,100% 100%,0 100%);"></div>
  <div class="cover-text" style="left:716px;top:201px;font-size:26px;">ENGINEERING</div>
  <div class="cover-text" style="left:677px;top:227px;font-size:35px;">CONSULTANT</div>
  <div class="sector-tag">GEOTECHNICAL &amp; UNDERGROUND SECTORS</div>

  <!-- INNER SHEET -->
  <div class="pocket" role="presentation"></div>
  <section class="sheet inner" aria-label="Lato interno della brochure">
    <!-- Our company -->
    <div class="photo" style="left:0;top:0;width:289px;height:217px;background:linear-gradient(160deg,#5f7a44 0%,#a3a093 35%,#bdb8ad 55%,#7d8a5a 80%,#4e6b3a 100%);" role="img" aria-label="Vista aerea di un cantiere all'imbocco di una galleria"></div>
    <div class="section-title" style="left:24px;top:184px;font-size:31px;letter-spacing:1px;"><b>OUR</b> COMPANY</div>
    <div class="photo" style="left:22px;top:239px;width:113px;height:72px;background:linear-gradient(180deg,#6b6257 0%,#8a7d6d 50%,#4e463e 100%);" role="img" aria-label="Escavatore al fronte di scavo in galleria"></div>
    <div class="photo" style="left:22px;top:320px;width:113px;height:72px;background:linear-gradient(180deg,#5c5752 0%,#8e8780 50%,#4a4540 100%);" role="img" aria-label="Interno di galleria con centine"></div>
    <div class="copy" style="left:153px;top:236px;width:101px;">
      <p>TIRO Engineering S.r.l. offre servizi di consulenza tecnica, contrattuale e strategica ai principali attori delle scienze geologiche, dell'ingegneria geotecnica e idraulica. Lavoriamo per ridurre rischio e incertezza, cercando con flessibilità la soluzione ottimale per il progetto.</p>
      <p>TIRO Engineering S.r.l. è una società indipendente nata nel luglio 2020 da un gruppo di professionisti con oltre trent'anni di esperienza nelle grandi opere di ingegneria civile, come direttori tecnici e liberi professionisti.</p>
      <p>I fondatori uniscono esperienza ed entusiasmo per una nuova realtà, con un obiettivo: infrastrutture safe, sustainable and economic.</p>
      <p>Each of our projects represents a long term commitment, we believe in providing safe, reliable, sustainable and innovative solutions. This is and will be our distinctive characteristic.</p>
    </div>

    <!-- Our services -->
    <div class="photo" style="left:289px;top:0;width:137px;height:182px;background:linear-gradient(180deg,#3a3a3a 0%,#6b6b6b 45%,#262626 100%);" role="img" aria-label="Galleria in bianco e nero con figura in controluce"></div>
    <div class="yellow" style="left:291px;top:18px;width:10px;height:41px;"></div>
    <div class="section-title" style="left:306px;top:19px;font-size:24px;"><b>OUR</b><br>SERVICES</div>
    <div class="copy copy-lg" style="left:446px;top:26px;width:107px;">
      <p>Progettazione e consulenza specialistica nel campo della geologia, dell'ingegneria geotecnica, delle opere sotterranee e dell'ingegneria idraulica.</p>
      <p>Aiutiamo i nostri clienti a risolvere problemi di natura progettuale, contrattuale e costruttiva che possono nascere nell'intera vita del progetto portando la nostra esperienza all'interno delle loro organizzazioni, migliorando la qualità dei loro servizi di ingegneria, ottimizzando i loro progetti, proponendo nuove idee e soluzioni.</p>
      <p>Tiro Engineering è in grado di fornire la propria assistenza nell'intero iter procedurale, dalla fase di indagine preliminare e di analisi di fattibilità fino alla progettazione costruttiva e all'assistenza tecnica in fase realizzativa.</p>
    </div>
    <!-- yellow frame -->
    <div class="yellow" style="left:276px;top:183px;width:13px;height:225px;"></div>
    <div class="yellow" style="left:276px;top:183px;width:160px;height:12px;clip-path:polygon(0 0,93% 0,100% 100%,0 100%);"></div>
    <div class="yellow-pale" style="left:432px;top:183px;width:24px;height:12px;clip-path:polygon(0 0,60% 0,100% 100%,40% 100%);"></div>
    <div class="yellow" style="left:410px;top:201px;width:164px;height:14px;clip-path:polygon(0 0,100% 0,100% 100%,12% 100%);"></div>
    <div class="yellow-pale" style="left:392px;top:201px;width:28px;height:14px;clip-path:polygon(0 0,40% 0,100% 100%,60% 100%);"></div>
    <div class="yellow" style="left:561px;top:0;width:13px;height:215px;"></div>
    <div class="copy" style="left:306px;top:236px;width:110px;">
      <p class="copy-lg" style="margin-bottom:8px;">La specializzazione e l'esperienza accumulate nelle discipline della geologia, dell'ingegneria geotecnica e del sottosuolo e dell'idraulica ci permette di massimizzare la nostra efficacia quando sia necessario:</p>
      <ul>
        <li>far fronte a situazioni di emergenza anche su progetti in fase di sviluppo avanzato garantendo l'immediata focalizzazione delle problematiche di progetto e il risultato finale atteso (in termini di qualità, tempistiche e costi...)</li>
        <li>fornire "second opinion" di elevato valore tecnico ed amministrativo in occasione di problematiche progettuali e costruttive e dispute legali</li>
        <li>analizzare in tempi brevi progetti svolti da terzi individuandone le "criticità", verificandone la cantierabilità e la validità tecnico economica.</li>
        <li>ottimizzare i progetti redatti da terzi implementandone il contenuto e massimizzando l'efficacia economica degli investimenti.</li>
      </ul>
    </div>
    <div class="photo" style="left:426px;top:221px;width:152px;height:187px;background:linear-gradient(180deg,#7d86a6 0%,#3e4668 40%,#2a2f4a 75%,#6f7490 100%);" role="img" aria-label="Scavo di galleria illuminato con mezzi al fronte"></div>

    <!-- Our expertise and experience -->
    <div class="photo" style="left:578px;top:0;width:109px;height:136px;background:linear-gradient(180deg,#9aa0a6 0%,#5d6368 50%,#8a7f6c 100%);" role="img" aria-label="Testa di una fresa meccanica per gallerie"></div>
    <div class="photo" style="left:687px;top:0;width:180px;height:136px;background:linear-gradient(180deg,#3d8fd8 0%,#6aa9de 45%,#b04a4e 60%,#7b7b80 85%,#9c8a6e 100%);" role="img" aria-label="Gru che solleva la testa di una fresa meccanica"></div>
    <div class="section-title" style="left:596px;top:86px;font-size:18px;"><b>OUR</b></div>
    <div class="section-title" style="left:596px;top:103px;font-size:11.5px;line-height:1.1;">EXPERTISE AND<br>EXPERIENCE</div>
    <div class="photo" style="left:687px;top:136px;width:180px;height:105px;background:var(--white);"></div>
    <div class="photo" style="left:693px;top:150px;width:166px;height:80px;background:linear-gradient(180deg,#b4b4b4 0%,#8a8a8a 100%);border-radius:30px 30px 2px 2px;" role="img" aria-label="Spazio per la foto del team"></div>
    <div class="copy" style="left:595px;top:148px;width:82px;">
      <p>La società nasce dall'associazione di un gruppo di professionisti, con indiscusse competenze ed affidabilità, con esperienza maturata in oltre trent'anni di attività come progettisti e consulenti nel settore delle grandi opere di ingegneria civile; geologia, ingegneria geotecnica ed idraulica ed opere sotterranee sono il "core" delle loro competenze.</p>
      <p style="font-weight:700;">I SOCI FONDATORI SONO:</p>
      <p>Paolo. Già Direttore Tecnico e Socio di Geostrade Srl fino al 2018, ha firmato tutti i progetti nel campo delle opere sotterranee e della geotecnica. Dal 2019 è Direttore Tecnico di Tecnoscavi. Vanta oltre 150 gallerie naturali, numerosi progetti ed assistenze tecniche nel campo delle strutture geotecniche, delle sistemazioni idrogeologiche e dei versanti. Negli ultimi dieci anni ha guidato attività di assistenza tecnica per opere di valore superiore a 440 Mio EUR e di progettazione per opere oltre 1.400 Mio EUR.</p>
      <p>Marco 30 anni di esperienza professionale. Coinvolto in più di 150 gallerie naturali con lunghezza complessiva superiore a 360 km. Numerosi progetti di assistenza tecnica nel campo delle strutture, delle sistemazioni idrogeologiche e dei versanti e delle opere di protezione ambientale.</p>
    </div>
    <div class="copy" style="left:702px;top:256px;width:148px;">
      <p>Negli ultimi dieci anni responsabile di attività di assistenza tecnica in corso d'opera per opere di valore superiore a 440 Mio EUR e di progettazione definitiva o esecutiva per opere oltre 1.400 Mio EUR, in Italia ed all'estero.</p>
      <p>Chiara 30 anni di esperienza professionale. Coinvolta in più di 150 gallerie naturali con lunghezza complessiva superiore a 360 km. Numerosi progetti di assistenza tecnica nel campo delle strutture, delle sistemazioni idrogeologiche, dei versanti e delle opere di protezione ambientale. Responsabile di verifiche ai fini della validazione, in Italia ed all'estero.</p>
      <p>Giulia 30 anni di esperienza professionale. Coinvolta in più di 150 gallerie naturali con lunghezza complessiva superiore a 360 km. Numerosi progetti di assistenza tecnica in corso d'opera e di progettazione definitiva o esecutiva, con attività di verifica per opere di valore complessivo superiore a 3.400 Mio EUR.</p>
    </div>
  </section>

</div>
</body>
</html>
```